Business Promotion A1 Poster

I need an A1 poster for a lift in my building. It needs to promote HarbourLeaf aa an employment expert for small business wanting to get their employment stuff right. We do on-site employment audits in Wellington for free.

We help small business manage the new 90 day trial period and help them design office/business policy manuals to avoid workplace problems.

The final design needs to convey expert and experience in employment. We use orange and grey as corporate colours. The company logo can be found on our website www.harbourleaf.co.nz

Target Market(s)

Small business owners and managers

Industry/Entity Type

Small Business

Requirements
Nice to have
• colour information experts employment law in NZ

```html
<!DOCTYPE html>
<html lang="en">
<head>
<meta charset="utf-8">
<title>HarbourLeaf – Empowering employers</title>
<link href="https://fonts.googleapis.com/css2?family=Arimo:wght@400;700&display=swap" rel="stylesheet">
<style>
  :root {
    --orange: #f39130;
    --grey-text: #b5b5b5;
    --white: #ffffff;
  }
  * { margin: 0; padding: 0; box-sizing: border-box; }
  html, body { width: 849px; height: 1200px; overflow: hidden; background: var(--white); }
  .poster {
    position: relative;
    width: 849px;
    height: 1200px;
    overflow: hidden;
    font-family: "Arimo", "Helvetica Neue", Arial, sans-serif;
    background: var(--white);
  }
  .hero-photo {
    position: absolute;
    left: 0; top: 0;
    width: 849px; height: 580px;
    background:
      radial-gradient(ellipse 260px 140px at 640px 500px, rgba(243,145,48,0.55), transparent 70%),
      radial-gradient(ellipse 220px 260px at 380px 170px, #e4e4e4, transparent 75%),
      radial-gradient(ellipse 420px 300px at 150px 420px, #cfcfcf, transparent 75%),
      linear-gradient(135deg, #bdbdbd 0%, #8d8d8d 40%, #4a4a4a 75%, #2e2e2e 100%);
  }
  .headline {
    position: absolute;
    z-index: 1;
    left: 80px;
    top: 396px;
    color: var(--orange);
    font-weight: 700;
    font-size: 100px;
    line-height: 92px;
    letter-spacing: -3.5px;
  }
  .info-band {
    position: absolute;
    z-index: 2;
    left: 0; top: 580px;
    width: 849px; height: 453px;
    background: var(--orange);
    color: var(--white);
    padding: 36px 0 0 84px;
  }
  .info-band .lead {
    font-weight: 700;
    font-size: 26.5px;
    line-height: 30px;
  }
  .services {
    list-style: none;
    margin-top: 15px;
    font-size: 27.5px;
    line-height: 32.7px;
  }
  .services li { position: relative; padding-left: 30px; }
  .services li::before {
    content: "";
    position: absolute;
    left: 2px; top: 13px;
    width: 9px; height: 9px;
    border-radius: 50%;
    background: var(--white);
  }
  .expertise { margin-top: 36px; }
  .expertise .title {
    font-weight: 700;
    font-size: 43px;
    line-height: 46px;
  }
  .expertise .subtitle {
    font-size: 27.5px;
    line-height: 32px;
  }
  .audit-offer {
    margin-top: 24px;
    font-weight: 700;
    font-size: 24px;
    line-height: 30px;
  }
  .brand {
    position: absolute;
    left: 84px;
    top: 1108px;
    display: flex;
    align-items: center;
    gap: 12px;
  }
  .brand-mark {
    width: 22px; height: 22px;
    background: var(--orange);
  }
  .brand-name {
    color: var(--orange);
    font-weight: 700;
    font-size: 30px;
    line-height: 36px;
  }
  .contact {
    position: absolute;
    right: 92px;
    top: 1046px;
    text-align: right;
  }
  .contact .prompt {
    color: var(--grey-text);
    font-size: 37.5px;
    line-height: 44px;
  }
  .contact .phone {
    color: var(--orange);
    font-size: 46px;
    line-height: 54px;
    margin-top: 8px;
  }
</style>
</head>
<body>
<main class="poster">
  <div class="hero-photo" role="img" aria-label="Close-up photograph of a brushed-metal jigsaw puzzle piece casting a shadow, lit with warm orange light"></div>
  <h1 class="headline">Empowering<br>employers</h1>
  <section class="info-band">
    <p class="lead">We will help your business</p>
    <ul class="services">
      <li>get the employment stuff right</li>
      <li>manage the 90 day trial period</li>
      <li>keep your employment agreements up to date</li>
      <li>manage restructure and redundancy</li>
      <li>get your business policies right</li>
    </ul>
    <div class="expertise">
      <p class="title">Experts</p>
      <p class="subtitle">in employment and recruitment</p>
    </div>
    <p class="audit-offer">Free on-site employment audits in Wellington</p>
  </section>
  <div class="brand">
    <span class="brand-mark"></span>
    <span class="brand-name">HarbourLeaf</span>
  </div>
  <footer class="contact">
    <p class="prompt">Call us today</p>
    <p class="phone">+64 4 5550182</p>
  </footer>
</main>
</body>
</html>
```